Young, dynamic furniture company needs a new business card design

We require a new business card design for our modern furniture company which supplies furniture and appliances to the property and development market.
Oakridge Interiors has become one of the leading furniture & appliance suppliers to the property market withing London. With over 10 years experience, we have increased our business to supply not only private landlords and managing agents, but also property developers, housing associations and local councils.
We offer not only a complete range of furniture which includes beds, wardrobes, dining sets and sofas, but also a high quality, full delivery and assembly service to help you with all our furnishing needs.

Target Market(s)

Private landlords, estate agents, letting agents, property management companies

Industry/Entity Type

Business

Contact Information for Business Card

Name,
Title,
Address,
Mobile,
Telephone,
Fax, Website, email address

Font styles to use
Sans Serif

Colors
3176b5
0555a3
85abd2
cfdeed

Requirements
Must have
• All the above information for each of our staff, along with our logo

```html
<!DOCTYPE html>
<html lang="en">
<head>
<meta charset="utf-8">
<title>Oakridge Interiors – Business Card</title>
<link href="https://fonts.googleapis.com/css2?family=Roboto:wght@400;500;700&display=swap" rel="stylesheet">
<style>
  :root{
    --bg:#1c1c1d;
    --card-white:#ffffff;
    --brand-blue:#0555a3;
    --brand-mid:#3176b5;
    --brand-light:#85abd2;
    --brand-pale:#cfdeed;
    --navy:#1d3a7a;
    --ink:#2b2b2e;
    --muted:#555a60;
  }
  *{box-sizing:border-box;margin:0;padding:0}
  html,body{width:1200px;height:923px;overflow:hidden;background:var(--bg);font-family:"Roboto",sans-serif}
  .canvas{position:relative;width:1200px;height:923px}
  .card{position:absolute;width:600px;height:343px;border-radius:22px;overflow:hidden;background:var(--card-white);box-shadow:0 14px 30px rgba(0,0,0,.55)}
  .card--back{left:520px;top:70px}
  .card--front{left:80px;top:500px}
  .card__bands{position:absolute;inset:0}
  .brand{position:absolute;display:flex;flex-direction:column;align-items:flex-start}
  .brand__row{display:flex;align-items:center;gap:10px}
  .brand__mark{width:22px;height:22px;background:var(--brand-blue)}
  .brand__name{font-weight:400;font-size:26px;letter-spacing:.5px;color:var(--ink);text-transform:uppercase}
  .brand__tagline{margin-top:4px;margin-left:32px;font-size:11px;letter-spacing:.6px;color:var(--muted);text-transform:uppercase}
  .card--back .brand{left:50%;top:120px;transform:translateX(-50%)}
  .back__web{position:absolute;left:0;right:0;top:230px;text-align:center;font-weight:500;font-size:15px;color:var(--ink)}
  .card--front .brand{left:120px;top:92px}
  .card--front .brand__name{font-size:22px}
  .contact{position:absolute;right:26px;top:150px;text-align:right;color:#fff;font-size:13.5px;line-height:18px}
  .contact__name{font-weight:700;font-size:19px;line-height:22px}
  .contact__title{margin-bottom:6px}
  .contact__address{margin-bottom:6px}
  .contact__line{display:flex;justify-content:flex-end;align-items:center;gap:8px}
  .contact__icon{width:14px;height:14px;flex:none}
</style>
</head>
<body>
<div class="canvas">

  <section class="card card--back" aria-label="Card back">
    <div class="brand">
      <div class="brand__row"><span class="brand__mark"></span><span class="brand__name">Oakridge Interiors</span></div>
      <span class="brand__tagline">Trade Furniture Solutions</span>
    </div>
    <p class="back__web">www.oakridgeinteriors.com</p>
  </section>

  <section class="card card--front" aria-label="Card front">
    <svg class="card__bands" viewBox="0 0 600 343" width="600" height="343" aria-hidden="true">
      <defs>
        <linearGradient id="topBand" x1="0" y1="1" x2="1" y2="0">
          <stop offset="0" stop-color="#1b4f9a"/>
          <stop offset="1" stop-color="#2a78c0"/>
        </linearGradient>
        <linearGradient id="lowBand" x1="0" y1="0" x2="1" y2="0">
          <stop offset="0" stop-color="#1f3f86"/>
          <stop offset=".2" stop-color="#7c8db3"/>
          <stop offset=".45" stop-color="#2f5a9a"/>
          <stop offset=".75" stop-color="#0555a3"/>
          <stop offset="1" stop-color="#0a4f9e"/>
        </linearGradient>
      </defs>
      <polygon points="0,0 300,0 0,185" fill="url(#topBand)"/>
      <polygon points="600,20 600,343 190,343" fill="url(#lowBand)"/>
    </svg>

    <div class="brand">
      <div class="brand__row"><span class="brand__mark"></span><span class="brand__name">Oakridge Interiors</span></div>
      <span class="brand__tagline">Trade Furniture Solutions</span>
    </div>

    <div class="contact">
      <p class="contact__name">Daniel Hart</p>
      <p class="contact__title">Job Title</p>
      <p>34 Street Name</p>
      <p class="contact__address">City Name, Country 4567</p>
      <p class="contact__line">000 1234 5678
        <svg class="contact__icon" viewBox="0 0 16 16" aria-label="Telephone"><path fill="#fff" d="M3 2h3l1 3-2 1c1 2 2 3 4 4l1-2 3 1v3c0 1-1 2-2 2C6 14 2 10 2 4c0-1 0-2 1-2z"/></svg></p>
      <p class="contact__line">000 1234 5678
        <svg class="contact__icon" viewBox="0 0 16 16" aria-label="Mobile"><rect x="4.5" y="1" width="7" height="14" rx="1.5" fill="none" stroke="#fff" stroke-width="1.5"/><circle cx="8" cy="12.5" r="1" fill="#fff"/></svg></p>
      <p class="contact__line">000 1234 5678
        <svg class="contact__icon" viewBox="0 0 16 16" aria-label="Fax"><rect x="4" y="1" width="8" height="4" fill="#fff"/><rect x="1" y="5" width="14" height="7" rx="1" fill="#fff"/><rect x="4" y="10" width="8" height="5" fill="#fff" stroke="#0555a3"/></svg></p>
      <p class="contact__line">info@oakridgeinteriors.com
        <svg class="contact__icon" viewBox="0 0 16 16" aria-label="Email"><rect x="1" y="3.5" width="14" height="9" fill="#fff"/><path d="M1 3.5l7 5 7-5" fill="none" stroke="#0555a3" stroke-width="1.2"/></svg></p>
      <p class="contact__line">www.oakridgeinteriors.com
        <svg class="contact__icon" viewBox="0 0 16 16" aria-label="Website"><circle cx="8" cy="8" r="6.5" fill="none" stroke="#fff" stroke-width="1.3"/><ellipse cx="8" cy="8" rx="3" ry="6.5" fill="none" stroke="#fff" stroke-width="1"/><path d="M1.5 8h13M3 4.5h10M3 11.5h10" stroke="#fff" stroke-width="1"/></svg></p>
    </div>
  </section>

</div>
</body>
</html>
```